Business IT Services Billboard to attract local small businesses

We are Brivoqua, a premier Managed Service Provider (MSP) specializing in comprehensive IT services and VOIP phone solutions exclusively for businesses. Our goal is to create a dynamic and visually engaging billboard advertisement that not only highlights our cutting-edge IT solutions but also emphasizes our state-of-the-art VOIP phone services. This billboard should communicate our commitment to providing innovative, reliable, and holistic technology solutions.
See the attached supporting documentation.
Target Market(s)
small business
Industry/Entity Type
Information Technology
Colors
Designer to choose colors to be used in the design.
Look and feel
Each slider illustrates characteristics of the customer's brand and the style your logo design should communicate.

```html
<!DOCTYPE html>
<html lang="en">
<head>
<meta charset="UTF-8">
<title>Brivoqua Billboard</title>
<link href="https://fonts.googleapis.com/css2?family=Poppins:wght@700;800&display=swap" rel="stylesheet">
<style>
  :root {
    --navy: #0c1a33;
    --blue: #1a74c4;
    --orange: #f08a1d;
    --white: #ffffff;
    --ink: #0c1a33;
    --page: #f2f3f5;
    --photo-a: #8a8f93;
    --photo-b: #c9b9a4;
  }
  * { margin: 0; padding: 0; box-sizing: border-box; }
  html, body {
    width: 944px;
    height: 1200px;
    overflow: hidden;
    background: var(--page);
    font-family: "Poppins", sans-serif;
  }
  .billboard {
    position: absolute;
    left: 22px;
    top: 469px;
    width: 900px;
    height: 262px;
    background: var(--white);
    box-shadow: 0 6px 18px rgba(0,0,0,0.18);
    overflow: hidden;
  }
  .headline-band {
    position: absolute;
    left: 0; top: 0;
    width: 100%;
    height: 195px;
    background: var(--navy);
  }
  .art {
    position: absolute;
    left: 0; top: 0;
  }
  .brand-name {
    position: absolute;
    left: 39px;
    top: 78px;
    font-weight: 800;
    font-size: 34px;
    line-height: 1;
    color: var(--blue);
    letter-spacing: -0.5px;
  }
  .headline {
    position: absolute;
    left: 203px;
    top: 26px;
    font-weight: 800;
    font-size: 30px;
    line-height: 33px;
    color: var(--white);
    text-transform: uppercase;
    white-space: nowrap;
  }
  .headline .accent { color: var(--blue); }
  .subline {
    position: absolute;
    left: 203px;
    top: 134px;
    font-weight: 700;
    font-size: 20px;
    line-height: 22px;
    color: var(--orange);
    white-space: nowrap;
  }
  .cta-lead {
    position: absolute;
    left: 37px;
    top: 208px;
    font-weight: 700;
    font-size: 16px;
    line-height: 19px;
    color: var(--ink);
    text-transform: uppercase;
    white-space: nowrap;
  }
  .web-icon {
    position: absolute;
    left: 239px;
    top: 220px;
  }
  .web-address {
    position: absolute;
    left: 261px;
    top: 208px;
    font-weight: 800;
    font-size: 28px;
    line-height: 38px;
    color: var(--ink);
    white-space: nowrap;
  }
</style>
</head>
<body>
  <section class="billboard">
    <div class="headline-band"></div>

    <svg class="art" width="900" height="262" viewBox="0 0 900 262">
      <defs>
        <linearGradient id="photoTone" x1="0" y1="0" x2="1" y2="1">
          <stop offset="0" stop-color="var(--photo-a)"/>
          <stop offset="1" stop-color="var(--photo-b)"/>
        </linearGradient>
      </defs>
      <polygon points="706,0 900,0 900,262 696,262 605,151" fill="var(--white)"/>
      <polyline points="704,0 603,151 694,262" fill="none" stroke="var(--blue)" stroke-width="3"/>
      <polygon class="team-photo" role="img"
        aria-label="Photo of a smiling support team wearing headsets working at computers"
        points="719,0 900,0 900,262 709,262 620,151" fill="url(#photoTone)"/>
    </svg>

    <div class="brand-name">Brivoqua</div>

    <h1 class="headline">
      Elevate your business<br>
      with next-gen IT and<br>
      <span class="accent">VOIP services</span>
    </h1>

    <p class="subline">IT and VOIP Solutions Tailored<br>for Your Business Success.</p>

    <p class="cta-lead">Transform your<br>tech today at</p>

    <svg class="web-icon" width="16" height="16" viewBox="0 0 16 16" aria-hidden="true">
      <circle cx="8" cy="8" r="7" fill="none" stroke="var(--blue)" stroke-width="1.5"/>
      <ellipse cx="8" cy="8" rx="3" ry="7" fill="none" stroke="var(--blue)" stroke-width="1.2"/>
      <line x1="1" y1="8" x2="15" y2="8" stroke="var(--blue)" stroke-width="1.2"/>
    </svg>
    <p class="web-address">WWW.BRIVOQUA.COM</p>
  </section>
</body>
</html>
```